Design the Business card for NetVaultic

Business card required for a professional Cyber Security business.
Company Logo and Icon has already been provided however I would like other options for the logo and icon to compare to. Alternatively, please refine/enhance the image of the logo.icon I have already provided.

If you are going to use the provided logo and icon, I was thinking that the company raised Logo on White background would serve well on the front of the card. See attached. AND, a large company raised stand-alone icon to appear on black background on the back of the card with tagline 'Cyber Risk Management, Governance and Consulting' or 'Cyber Security for your Business' See attached.
Alternatively, provide your own design for the logo and icon.

Target Market(s)

Enterprise, Government, Financial.

Contact Information for Business Card

Tavin Orloweth
Founder and CEO

Email Address
Mobile Number
Website URL
LinkedIn URL

Logo Text

NetVaultic - see attached example of logo

Font styles to use
Other font styles liked:
• Berlin Sans FB

Requirements
Must have
• Clean large and bold icon on the back with tagline.
• Horizontal alignment,
Nice to have
• Round edges.
• Raised Logo/Icon
Should not have
• An unprofessional look and feel.

```html
<!DOCTYPE html>
<html lang="en">
<head>
<meta charset="utf-8">
<title>NetVaultic Business Card</title>
<link rel="stylesheet" href="https://fonts.googleapis.com/css2?family=Cabin:wght@500;600;700&family=Roboto:wght@400&display=swap">
<style>
  :root {
    --backdrop: #2b2b2d;
    --card-white: #f2f2f2;
    --card-black: #1b1c1e;
    --brand-blue: #0a6bb8;
    --mark-blue: #3f6fc4;
    --accent-gold: #f2b705;
    --text-grey: #474747;
    --line-white: #ffffff;
  }
  html, body {
    margin: 0;
    padding: 0;
    width: 1200px;
    height: 960px;
    overflow: hidden;
    background: var(--backdrop);
  }
  .canvas {
    position: relative;
    width: 1200px;
    height: 960px;
  }
  .card {
    position: absolute;
    left: 313px;
    width: 600px;
    height: 342px;
    box-shadow: 0 4px 10px rgba(0,0,0,0.5);
    overflow: hidden;
  }
  .card-front { top: 113px; background: var(--card-white); }
  .card-back { top: 473px; height: 341px; width: 598px; background: var(--card-black); }
  .front-arc { position: absolute; left: 0; top: 0; }
  .holder {
    position: absolute;
    left: 34px;
    top: 20px;
    font-family: "Cabin", sans-serif;
  }
  .holder-name {
    margin: 0;
    color: var(--accent-gold);
    font-size: 20px;
    font-weight: 600;
    line-height: 26px;
  }
  .holder-role {
    margin: 0;
    color: var(--line-white);
    font-size: 14px;
    font-weight: 500;
    line-height: 18px;
  }
  .contact-list {
    position: absolute;
    right: 52px;
    top: 120px;
    margin: 0;
    padding: 0;
    list-style: none;
    font-family: "Roboto", sans-serif;
    font-size: 14px;
    color: var(--text-grey);
    text-align: right;
  }
  .contact-list li {
    display: flex;
    justify-content: flex-end;
    align-items: center;
    gap: 8px;
    height: 19.3px;
  }
  .contact-icon { width: 13px; height: 13px; flex: none; }
  .brand-front {
    position: absolute;
    left: 232px;
    top: 216px;
    display: flex;
    align-items: center;
    gap: 12px;
  }
  .brand-dot {
    width: 70px;
    height: 70px;
    border-radius: 50%;
    background: var(--mark-blue);
  }
  .brand-name {
    font-family: "Cabin", sans-serif;
    font-weight: 700;
    font-size: 42px;
    color: var(--brand-blue);
    line-height: 1;
  }
  .brand-back {
    position: absolute;
    left: 0;
    right: 0;
    top: 56px;
    display: flex;
    flex-direction: column;
    align-items: center;
    gap: 16px;
  }
  .brand-back .brand-dot { width: 130px; height: 130px; }
  .brand-back .brand-name { font-size: 30px; color: var(--mark-blue); }
  .tagline {
    position: absolute;
    left: 0;
    right: 0;
    top: 276px;
    margin: 0;
    text-align: center;
    font-family: "Cabin", sans-serif;
    font-weight: 500;
    font-size: 17px;
    color: var(--mark-blue);
  }
  .tagline-accent { color: var(--accent-gold); }
</style>
</head>
<body>
<main class="canvas">
  <section class="card card-front" aria-label="Card front">
    <svg class="front-arc" width="600" height="342" viewBox="0 0 600 342" aria-hidden="true">
      <path d="M0 0 H350 Q40 50 6 342 H0 Z" fill="var(--brand-blue)"/>
      <path d="M346 6 Q36 50 6 330" fill="none" stroke="var(--line-white)" stroke-width="1.6"/>
      <circle cx="347" cy="9" r="8" fill="var(--line-white)" stroke="var(--brand-blue)" stroke-width="3"/>
      <circle cx="7" cy="332" r="8" fill="var(--line-white)" stroke="var(--brand-blue)" stroke-width="3"/>
    </svg>

    <div class="holder">
      <p class="holder-name">Tavin Orloweth</p>
      <p class="holder-role">Founder &amp; CEO</p>
    </div>

    <ul class="contact-list">
      <li>604 218 7391
        <svg class="contact-icon" viewBox="0 0 13 13" aria-hidden="true"><rect x="3" y="0.5" width="7" height="12" rx="1.2" fill="none" stroke="var(--brand-blue)" stroke-width="1.4"/><line x1="5.5" y1="10.5" x2="7.5" y2="10.5" stroke="var(--brand-blue)" stroke-width="1.2"/></svg>
      </li>
      <li>tavin@netvaultic.com
        <svg class="contact-icon" viewBox="0 0 13 13" aria-hidden="true"><rect x="0.5" y="2.5" width="12" height="8" fill="var(--brand-blue)"/><path d="M1 3 L6.5 7.5 L12 3" fill="none" stroke="var(--line-white)" stroke-width="1"/></svg>
      </li>
      <li>www.netvaultic.com
        <svg class="contact-icon" viewBox="0 0 13 13" aria-hidden="true"><circle cx="6.5" cy="6.5" r="6" fill="var(--brand-blue)"/><ellipse cx="6.5" cy="6.5" rx="2.5" ry="6" fill="none" stroke="var(--line-white)" stroke-width="0.9"/><line x1="0.5" y1="6.5" x2="12.5" y2="6.5" stroke="var(--line-white)" stroke-width="0.9"/></svg>
      </li>
      <li>netvaultic
        <svg class="contact-icon" viewBox="0 0 13 13" aria-hidden="true"><circle cx="6.5" cy="6.5" r="6" fill="var(--brand-blue)"/></svg>
      </li>
    </ul>

    <div class="brand-front">
      <span class="brand-dot" aria-hidden="true"></span>
      <span class="brand-name">NetVaultic</span>
    </div>
  </section>

  <section class="card card-back" aria-label="Card back">
    <div class="brand-back">
      <span class="brand-dot" aria-hidden="true"></span>
      <span class="brand-name">NetVaultic</span>
    </div>
    <p class="tagline">Cyber Risk Management, <span class="tagline-accent">Governance &amp; Consulting</span></p>
  </section>
</main>
</body>
</html>
```